VOMRA Pty Ltd Business Card

Looking for a simple yet eye-catching double-sided business card design using my company logo on one side and contact details on the other.

Target Market(s)

Government

Industry/Entity Type

Communication Systems Engineering

Contact Information for Business Card

VOMRA Pty Ltd

Requirements
Nice to have
• Would be great to have a QR code so details can be scanned into contacts

```html
<!DOCTYPE html>
<html lang="en">
<head>
<meta charset="utf-8">
<title>VOMRA Pty Ltd Business Card</title>
<link href="https://fonts.googleapis.com/css2?family=Open+Sans:wght@400;700;800&display=swap" rel="stylesheet">
<style>
  :root {
    --page: #2b2f34;
    --card: #ffffff;
    --ink: #37414a;
    --text: #1e2226;
    --shadow: rgba(0,0,0,0.45);
  }
  * { margin: 0; padding: 0; box-sizing: border-box; }
  html, body { width: 1200px; height: 780px; overflow: hidden; }
  body {
    background: var(--page);
    font-family: "Open Sans", Arial, sans-serif;
    position: relative;
  }
  .card {
    position: absolute;
    width: 540px;
    height: 309px;
    background: var(--card);
    box-shadow: 0 12px 30px var(--shadow);
    overflow: hidden;
  }
  .card--contact { left: 40px; top: 236px; }
  .card--brand { left: 620px; top: 236px; }

  .brand-name {
    position: absolute;
    display: flex;
    align-items: center;
    color: var(--ink);
    font-weight: 800;
    letter-spacing: 1px;
  }
  .brand-name .dot {
    display: inline-block;
    border-radius: 50%;
    background: var(--ink);
  }
  .card--contact .brand-name { left: 120px; top: 22px; font-size: 44px; gap: 14px; }
  .card--contact .brand-name .dot { width: 16px; height: 16px; }
  .card--brand .brand-name { left: 0; right: 0; top: 100px; justify-content: center; font-size: 84px; gap: 24px; }
  .card--brand .brand-name .dot { width: 28px; height: 28px; }

  .holder {
    position: absolute;
    right: 66px;
    top: 98px;
    text-align: right;
    color: var(--ink);
  }
  .holder__name { font-size: 26px; font-weight: 700; line-height: 1.1; }
  .holder__role { font-size: 14px; color: var(--text); margin-top: 2px; }

  .tab { position: absolute; right: 0; top: 96px; }

  .contact-list {
    position: absolute;
    left: 26px;
    top: 120px;
    list-style: none;
    font-size: 13px;
    line-height: 1.45;
    color: var(--text);
  }
  .contact-list li { display: flex; align-items: center; gap: 6px; }
  .contact-list .address { display: block; padding-left: 18px; margin-bottom: 2px; }
  .contact-list svg { width: 12px; height: 12px; flex: none; fill: var(--ink); }
</style>
</head>
<body>
  <section class="card card--contact">
    <div class="brand-name"><span class="dot"></span>VOMRA</div>

    <ul class="contact-list">
      <li class="address">14-16 Harlow Lane Redfern<br>NSW 2016 Australia</li>
      <li>
        <svg viewBox="0 0 12 12" aria-hidden="true"><path d="M2.5 1l2 2.2-1 1.3a6 6 0 0 0 4 4l1.3-1 2.2 2-1.3 1.5C5.5 11 1 6.5 1 2.3z"/></svg>
        (817) 555-0142
      </li>
      <li>
        <svg viewBox="0 0 12 12" aria-hidden="true"><circle cx="6" cy="6" r="5.2" fill="none" stroke="#37414a" stroke-width="1.2"/><path d="M1 6h10M6 1c-2.5 3-2.5 7 0 10M6 1c2.5 3 2.5 7 0 10" fill="none" stroke="#37414a" stroke-width="1"/></svg>
        www.vomra.com.au
      </li>
      <li>
        <svg viewBox="0 0 12 12" aria-hidden="true"><rect x="0.5" y="2.5" width="11" height="7.5" rx="1"/><path d="M1 3l5 4 5-4" fill="none" stroke="#fff" stroke-width="1"/></svg>
        admin@vomra.com.au
      </li>
    </ul>

    <div class="holder">
      <div class="holder__name">Jordan Mercer</div>
      <div class="holder__role">Co-Founder</div>
    </div>

    <svg class="tab" width="50" height="70" viewBox="0 0 50 70" aria-hidden="true">
      <path d="M18 0H50V70H4V50H12V30H18Z" fill="var(--ink)"/>
    </svg>
  </section>

  <section class="card card--brand">
    <div class="brand-name"><span class="dot"></span>VOMRA</div>
  </section>
</body>
</html>
```